Vellisant - Quality health delivered at your door

Vellisant offers home and Community Based Services for adults who wish to continue live independently in their communities. We increase accessibility to health care, reduce health care delivery gap, reduce mortality and morbidity, reduce health while promoting healthy living in the comfort of our patients communities or homes.

We provide on site services and deliver high quality healthcare at your door. Our experienced physicians coordinate care with our certified nurse practitioners and provide chronic care management, physical therapy, rehabilitation and medications management.

Target Market(s)

Older population living in independent living facilities

Industry/Entity Type

Health Care

Contact Information for Business Card

Vellisant

Number of Pages Required

4 page

Font styles to use
Sans Serif

Colors

Designer to choose colors to be used in the design.

```html
<!DOCTYPE html>
<html lang="en">
<head>
<meta charset="utf-8">
<title>Vellisant – Quality health delivered at your door</title>
<link href="https://fonts.googleapis.com/css2?family=Raleway:wght@400;500;600;700&family=Open+Sans:wght@400;600;700&display=swap" rel="stylesheet">
<style>
:root{
  --orange:#f7a21b;
  --orange-dark:#e8900a;
  --green:#3f6b14;
  --green-dark:#2f5410;
  --ink:#2f2f2f;
  --text:#7a7a7a;
  --line:#e6e6e6;
  --white:#ffffff;
}
*{margin:0;padding:0;box-sizing:border-box}
html,body{width:1200px;height:3982px;overflow:hidden;background:var(--white)}
body{font-family:"Open Sans",Arial,sans-serif;color:var(--text);position:relative}
.abs{position:absolute}
.top-rule{left:0;top:0;width:1200px;height:5px;background:linear-gradient(90deg,var(--green) 0 60%,var(--orange) 60% 100%)}

/* brand */
.brand{display:flex;flex-direction:column;align-items:center;width:175px}
.brand-dot{width:86px;height:86px;border-radius:50%;background:var(--orange);border:5px solid var(--green)}
.brand-name{font-family:"Raleway",sans-serif;font-weight:700;font-size:26px;color:var(--green);margin-top:6px;letter-spacing:.5px}

/* header */
.site-header .brand{left:98px;top:36px}
.contact-chip{display:flex;align-items:center;gap:14px;font-size:13px;line-height:18px;color:#666}
.chip-icon{width:44px;height:44px;border-radius:50%;border:2px solid var(--green);display:flex;align-items:center;justify-content:center;flex:none}
.social{display:flex;gap:10px}
.social span{width:36px;height:36px;border-radius:50%;border:3px solid var(--green);display:block}
.social span:nth-child(2){border-color:#2a9bd7}
.social span:nth-child(3){border-color:#3a6aa0}
.social span:nth-child(4){border-color:#c8302b}

/* hero */
.hero{left:0;top:172px;width:1200px;height:492px;clip-path:polygon(0 70px,24% 0,76% 0,100% 70px,100% 100%,0 100%);
  background:linear-gradient(100deg,#4a5f63 0%,#8aa0a6 22%,#b58f76 45%,#8e6a52 60%,#c9a489 80%,#6f5040 100%)}
.hero-title{left:478px;top:318px;font-family:"Raleway",sans-serif;font-weight:700;font-size:70px;letter-spacing:5px;color:var(--white)}
.hero-sub{left:478px;top:416px;width:580px;font-size:15px;line-height:24px;color:var(--white)}
.hero-btn{left:677px;top:499px;width:117px;height:45px;border:2px solid var(--white);color:var(--white);font-family:"Raleway",sans-serif;font-weight:700;font-size:12px;display:flex;align-items:center;justify-content:center;letter-spacing:.5px}

/* nav */
.main-nav{left:0;top:664px;width:1200px;height:48px;background:var(--orange);display:flex;align-items:center;padding-left:98px}
.main-nav a{font-family:"Raleway",sans-serif;font-weight:700;font-size:12px;color:var(--white);text-decoration:none;height:48px;display:flex;align-items:center;padding:0 20px;letter-spacing:.3px}
.main-nav a.current{background:var(--green)}

/* headings */
.section-title{left:0;width:1200px;text-align:center;font-family:"Raleway",sans-serif;font-weight:500;font-size:36px;letter-spacing:3px;color:var(--ink)}
.read-more{font-size:12px;color:var(--ink);display:flex;align-items:center;justify-content:center;gap:7px}
.read-more i{width:13px;height:13px;border-radius:50%;background:var(--ink);display:inline-flex;align-items:center;justify-content:center}
.read-more.accent{color:var(--orange)}
.read-more.accent i{background:var(--orange)}

/* welcome */
.welcome-text{left:250px;top:852px;width:700px;text-align:center;font-size:13px;line-height:25px}
.care-card{top:950px;width:318px;height:420px;border:1px solid var(--line);background:var(--white)}
.care-photo{height:242px}
.care-card h3{font-family:"Raleway",sans-serif;font-weight:600;font-size:19px;color:var(--ink);text-align:center;margin-top:32px}
.care-card p{font-size:12px;line-height:18px;text-align:center;margin:12px 34px 14px}

/* band */
.promise-band{left:0;top:1452px;width:1200px;height:380px;clip-path:polygon(0 0,100% 0,100% 62%,50% 100%,0 62%);
  background:linear-gradient(120deg,#7a5a46 0%,#b8917a 40%,#d7b9a4 60%,#8a6a55 100%)}
.band-text{left:0;top:1538px;width:1200px;text-align:center;font-family:"Raleway",sans-serif;font-weight:500;font-size:35px;line-height:59px;color:var(--white)}
.btn{background:var(--orange);color:var(--white);font-family:"Raleway",sans-serif;font-weight:700;font-size:12px;letter-spacing:.5px;display:flex;align-items:center;justify-content:center}

/* services */
.service{width:290px;text-align:center}
.service-icon{width:138px;height:138px;border-radius:50%;border:5px solid var(--green);background:var(--orange);margin:0 auto;display:flex;align-items:center;justify-content:center}
.service-icon.alt{background:var(--green);border-color:var(--orange)}
.service h3{font-family:"Raleway",sans-serif;font-weight:700;font-size:15px;color:var(--ink);line-height:20px;margin-top:32px;min-height:20px}
.service p{font-size:12px;line-height:18px;margin:10px 14px 16px}

/* news */
.news{left:0;top:2867px;width:1200px;height:700px;clip-path:polygon(0 0,100% 0,100% 82%,72% 100%,28% 100%,0 82%);
  background:linear-gradient(110deg,#3d2c24 0%,#7d6a5f 35%,#a98f7c 55%,#5f4332 80%,#2e211b 100%)}
.news .shade{position:absolute;inset:0;background:rgba(0,0,0,.18)}
.news-title{color:var(--white);top:2935px}
.news-card{top:3029px;width:318px;height:303px;background:var(--white);border-top:5px solid var(--orange);text-align:center}
.news-card .month{font-family:"Raleway",sans-serif;font-weight:500;font-size:24px;color:var(--ink);margin-top:36px}
.news-card .year{font-family:"Raleway",sans-serif;font-weight:600;font-size:44px;color:var(--ink);line-height:50px}
.news-card p{font-size:12px;line-height:18px;margin:16px 24px 16px}

/* footer */
.site-footer .brand{left:98px;top:3659px}
.foot-head{font-family:"Raleway",sans-serif;font-weight:700;font-size:15px;color:var(--ink);letter-spacing:.5px}
.foot-note{font-size:11px;color:var(--text)}
.mail-field{width:258px;height:42px;border:1px solid var(--line);font-size:11px;color:#aaa;display:flex;align-items:center;padding-left:16px}
.foot-row{display:flex;align-items:flex-start;gap:16px;font-size:13px;line-height:20px;color:#666}
.foot-row svg{flex:none;margin-top:2px}
.foot-rule{left:98px;top:3892px;width:1004px;height:1px;background:var(--line)}
.copyright{left:0;top:3927px;width:1200px;text-align:center;font-size:11px;color:#777}
</style>
</head>
<body>

<div class="abs top-rule"></div>

<header class="site-header">
  <div class="abs brand"><span class="brand-dot"></span><span class="brand-name">VELLISANT</span></div>
  <div class="abs contact-chip" style="left:393px;top:74px">
    <span class="chip-icon"><svg width="16" height="20" viewBox="0 0 16 20"><path d="M8 1a6 6 0 0 1 6 6c0 5-6 12-6 12S2 12 2 7a6 6 0 0 1 6-6z" fill="none" stroke="#3f6b14" stroke-width="2"/><circle cx="8" cy="7" r="2" fill="#3f6b14"/></svg></span>
    <span>23GT, quis nostrud exercitation<br>ullamco laboris</span>
  </div>
  <div class="abs contact-chip" style="left:677px;top:74px">
    <span class="chip-icon"><svg width="18" height="18" viewBox="0 0 18 18"><path d="M4 1l3 4-2 2c1 3 3 5 6 6l2-2 4 3-2 3C8 17 1 10 1 3z" fill="#3f6b14"/></svg></span>
    <span>(555) - 014 - 2286<br>hello@vellisant.example</span>
  </div>
  <div class="abs social" style="left:930px;top:80px"><span></span><span></span><span></span><span></span></div>
</header>

<section class="abs hero" role="img" aria-label="Photo of a smiling nurse in blue scrubs checking an older woman's blood pressure at home"></section>
<div class="abs hero-title">VELLISANT</div>
<p class="abs hero-sub">Vellisant offers home and Community Based Services for adults who wish to continue live independently in their communities.</p>
<div class="abs hero-btn">READ MORE</div>

<nav class="abs main-nav">
  <a class="current">HOME</a>
  <a>ASSISTED LIVING</a>
  <a>SKILLED NURSING</a>
  <a>INDEPENDENT LIVING</a>
  <a>HOME&amp;COMMUNITY BASED SERVICES</a>
  <a>MORE</a>
  <a><svg width="14" height="14" viewBox="0 0 14 14"><circle cx="6" cy="6" r="4.5" fill="none" stroke="#fff" stroke-width="2"/><path d="M9.5 9.5L13 13" stroke="#fff" stroke-width="2"/></svg></a>
</nav>

<section class="welcome">
  <h2 class="abs section-title" style="top:786px">WELCOME TO VELLISANT</h2>
  <p class="abs welcome-text">Vellisant offers home and Community Based Services for adults who wish to continue to live independently in the comfort of their communities. We provide on site services and deliver high quality healthcare at your door.</p>

  <article class="abs care-card" style="left:98px">
    <div class="care-photo" role="img" aria-label="Photo of an older woman and a younger carer smiling together" style="background:linear-gradient(135deg,#6b4a3a,#b98c6e 50%,#e2c7a8)"></div>
    <h3>Personal Care</h3>
    <p>Warm help with bathing, dressing and meals so every day feels calm at home.</p>
    <div class="read-more">Read More <i><svg width="7" height="7" viewBox="0 0 7 7"><path d="M2 1l3 2.5L2 6" fill="none" stroke="#fff" stroke-width="1.4"/></svg></i></div>
  </article>
  <article class="abs care-card" style="left:441px">
    <div class="care-photo" role="img" aria-label="Photo of an older man with a cane being visited by a carer outdoors" style="background:linear-gradient(135deg,#7f9a5a,#c4cf9a 45%,#5b7aa0)"></div>
    <h3>Monitoring visits</h3>
    <p>Regular nurse visits check vitals, review medicines and keep your doctor informed.</p>
    <div class="read-more">Read More <i><svg width="7" height="7" viewBox="0 0 7 7"><path d="M2 1l3 2.5L2 6" fill="none" stroke="#fff" stroke-width="1.4"/></svg></i></div>
  </article>
  <article class="abs care-card" style="left:781px">
    <div class="care-photo" role="img" aria-label="Photo of a carer walking arm in arm with an older woman indoors" style="background:linear-gradient(135deg,#d8d2c6,#9d8b79 50%,#3e3530)"></div>
    <h3>Dementia care</h3>
    <p>Patient, trained carers offer memory support, safe routines and kind company daily.</p>
    <div class="read-more">Read More <i><svg width="7" height="7" viewBox="0 0 7 7"><path d="M2 1l3 2.5L2 6" fill="none" stroke="#fff" stroke-width="1.4"/></svg></i></div>
  </article>
</section>

<section class="abs promise-band" role="img" aria-label="Close photo of a carer's hands holding an older person's hands"></section>
<p class="abs band-text">We provide on site services and deliver high<br>quality healthcare at your door</p>
<div class="abs btn" style="left:483px;top:1694px;width:234px;height:48px">CONTACT US NOW !</div>

<section class="services">
  <h2 class="abs section-title" style="top:1934px">OUR SERVICES</h2>

  <div class="abs service" style="left:120px;top:2023px">
    <div class="service-icon"><svg width="60" height="60" viewBox="0 0 60 60" fill="none" stroke="#fff" stroke-width="4" stroke-linecap="round"><path d="M14 8v16a12 12 0 0 0 24 0V8"/><path d="M26 36v6a10 10 0 0 0 20 0v-8"/><circle cx="46" cy="28" r="5"/></svg></div>
    <h3>Comprehensive primary<br>care services</h3>
    <p>Checkups and chronic care plans led by our visiting physicians.</p>
    <div class="read-more">Read More <i><svg width="7" height="7" viewBox="0 0 7 7"><path d="M2 1l3 2.5L2 6" fill="none" stroke="#fff" stroke-width="1.4"/></svg></i></div>
  </div>
  <div class="abs service" style="left:452px;top:2023px">
    <div class="service-icon alt"><svg width="60" height="60" viewBox="0 0 60 60" fill="#fff"><circle cx="22" cy="16" r="7"/><circle cx="40" cy="20" r="6"/><path d="M10 48c0-12 5-20 12-20s12 8 12 20z"/><path d="M30 48c1-10 4-16 10-16s10 6 10 16z"/></svg></div>
    <h3>Social services<br>assessment</h3>
    <p>We review needs and link families to local support programs.</p>
    <div class="read-more accent">Read More <i><svg width="7" height="7" viewBox="0 0 7 7"><path d="M2 1l3 2.5L2 6" fill="none" stroke="#fff" stroke-width="1.4"/></svg></i></div>
  </div>
  <div class="abs service" style="left:784px;top:2023px">
    <div class="service-icon"><svg width="58" height="52" viewBox="0 0 58 52" fill="#fff"><path d="M29 2L2 26h8v24h14V34h10v16h14V26h8z"/></svg></div>
    <h3>Home health assistance</h3>
    <p>Nurses bring wound care, medicines and monitoring right to your home.</p>
    <div class="read-more">Read More <i><svg width="7" height="7" viewBox="0 0 7 7"><path d="M2 1l3 2.5L2 6" fill="none" stroke="#fff" stroke-width="1.4"/></svg></i></div>
  </div>

  <div class="abs service" style="left:120px;top:2371px">
    <div class="service-icon"><svg width="60" height="60" viewBox="0 0 60 60" fill="#fff"><circle cx="30" cy="12" r="7"/><rect x="8" y="34" width="44" height="8" rx="3"/><rect x="12" y="42" width="4" height="10"/><rect x="44" y="42" width="4" height="10"/><path d="M22 22h16l4 10H18z"/></svg></div>
    <h3>Physical therapy</h3>
    <p>Gentle exercise plans that rebuild strength, balance and daily mobility at home.</p>
    <div class="read-more">Read More <i><svg width="7" height="7" viewBox="0 0 7 7"><path d="M2 1l3 2.5L2 6" fill="none" stroke="#fff" stroke-width="1.4"/></svg></i></div>
  </div>
  <div class="abs service" style="left:452px;top:2371px">
    <div class="service-icon alt"><svg width="60" height="60" viewBox="0 0 60 60" fill="none" stroke="#fff" stroke-width="4" stroke-linejoin="round"><path d="M14 26a16 16 0 1 1 24 14v10H22v-6h-6v-8l-4-2z"/><path d="M28 18v14M22 24h12"/></svg></div>
    <h3>Mental health</h3>
    <p>Caring counselors support mood, memory and wellbeing through regular talks.</p>
    <div class="read-more accent">Read More <i><svg width="7" height="7" viewBox="0 0 7 7"><path d="M2 1l3 2.5L2 6" fill="none" stroke="#fff" stroke-width="1.4"/></svg></i></div>
  </div>
  <div class="abs service" style="left:784px;top:2371px">
    <div class="service-icon"><svg width="50" height="60" viewBox="0 0 50 60" fill="#fff"><path d="M12 4c6 0 8 3 13 3s7-3 13-3c8 0 10 8 9 16-1 10-5 14-6 24-1 8-3 13-6 13s-4-6-5-12c-1-5-2-7-5-7s-4 2-5 7c-1 6-2 12-5 12s-5-5-6-13C8 34 4 30 3 20 2 12 4 4 12 4z"/></svg></div>
    <h3>Dental health</h3>
    <p>Routine cleanings and mouth checks arranged around your own schedule.</p>
    <div class="read-more">Read More <i><svg width="7" height="7" viewBox="0 0 7 7"><path d="M2 1l3 2.5L2 6" fill="none" stroke="#fff" stroke-width="1.4"/></svg></i></div>
  </div>

  <div class="abs btn" style="left:483px;top:2732px;width:234px;height:53px">VIEW ALL SERVICES</div>
</section>

<section class="abs news" role="img" aria-label="Photo of a carer leaning close to an older woman in a wheelchair"><div class="shade"></div></section>
<h2 class="abs section-title news-title">OUR LATEST NEWS</h2>

<article class="abs news-card" style="left:98px">
  <div class="month">MARCH</div><div class="year">2017</div>
  <p>Our new nurse team now covers three more neighborhoods, bringing visits closer to home.</p>
  <div class="read-more">Read More <i><svg width="7" height="7" viewBox="0 0 7 7"><path d="M2 1l3 2.5L2 6" fill="none" stroke="#fff" stroke-width="1.4"/></svg></i></div>
</article>
<article class="abs news-card" style="left:441px">
  <div class="month">JUNE</div><div class="year">2017</div>
  <p>Summer wellness days offered free balance checks and healthy cooking tips for seniors.</p>
  <div class="read-more">Read More <i><svg width="7" height="7" viewBox="0 0 7 7"><path d="M2 1l3 2.5L2 6" fill="none" stroke="#fff" stroke-width="1.4"/></svg></i></div>
</article>
<article class="abs news-card" style="left:781px">
  <div class="month">JULY</div><div class="year">2017</div>
  <p>We partnered with local pharmacies to simplify medicine delivery for every patient.</p>
  <div class="read-more">Read More <i><svg width="7" height="7" viewBox="0 0 7 7"><path d="M2 1l3 2.5L2 6" fill="none" stroke="#fff" stroke-width="1.4"/></svg></i></div>
</article>

<footer class="site-footer">
  <div class="abs brand"><span class="brand-dot"></span><span class="brand-name">VELLISANT</span></div>

  <div class="abs" style="left:329px;top:3656px">
    <div class="foot-head">SUBSCRIBE TO NEWSLETTER</div>
    <div class="foot-note" style="margin-top:20px">Get care tips and news in your inbox.</div>
    <div class="mail-field" style="margin-top:20px">Enter Mail....</div>
    <div class="btn" style="width:110px;height:42px;margin-top:16px;font-size:11px">SUBSCRIBE</div>
  </div>

  <div class="abs" style="left:642px;top:3656px">
    <div class="foot-head">CONTACT US</div>
    <div class="foot-row" style="margin-top:22px">
      <svg width="14" height="18" viewBox="0 0 16 20"><path d="M8 1a6 6 0 0 1 6 6c0 5-6 12-6 12S2 12 2 7a6 6 0 0 1 6-6z" fill="none" stroke="#3f6b14" stroke-width="2"/><circle cx="8" cy="7" r="2" fill="#3f6b14"/></svg>
      <span>23GT, quis nostrud exercition<br>ullamco laboris</span>
    </div>
    <div class="foot-row" style="margin-top:16px">
      <svg width="16" height="16" viewBox="0 0 18 18"><path d="M4 1l3 4-2 2c1 3 3 5 6 6l2-2 4 3-2 3C8 17 1 10 1 3z" fill="#3f6b14"/></svg>
      <span>(555) - 014 - 2286</span>
    </div>
    <div class="foot-row" style="margin-top:16px">
      <svg width="16" height="12" viewBox="0 0 16 12"><rect x="1" y="1" width="14" height="10" fill="none" stroke="#3f6b14" stroke-width="1.6"/><path d="M1 1l7 6 7-6" fill="none" stroke="#3f6b14" stroke-width="1.6"/></svg>
      <span>hello@vellisant.example</span>
    </div>
  </div>

  <div class="abs" style="left:929px;top:3656px">
    <div class="foot-head">FOLLOW US</div>
    <div class="social" style="margin-top:28px"><span></span><span></span><span></span><span></span></div>
  </div>

  <div class="abs foot-rule"></div>
  <p class="abs copyright">© copyright 2017 Vellisant. All Rights Reserved</p>
</footer>

</body>
</html>
```